Looking for a modern, Professional business card design

We have a simple business card, but are looking for a more modern, professional look. A sample of the basic card is attached as well as the logo. We would also like to add that we offer:
Struggling with your finances?
- Learn to become debt free
- Discover the power of cash
- Control your money instead of it controlling you
Let us help you achieve a new level of financial freedom!
Also, we would like to have a "SPECIAL OFFER!: FREE 30 minute consultation"
Financial Planning

```html
<!DOCTYPE html>
<html lang="en">
<head>
<meta charset="utf-8">
<title>Liberty Path Money Coaching – Business Cards</title>
<link rel="stylesheet" href="https://fonts.googleapis.com/css2?family=Roboto:wght@300;400;700&family=Roboto+Condensed:wght@700&display=swap">
<style>
  :root {
    --bg: #ebe8e2;
    --card-white: #ffffff;
    --card-shade: #eef0ec;
    --green-dark: #3f9a35;
    --green-mid: #6cba48;
    --green-light: #b9dc6a;
    --green-pale: #dcebc8;
    --ink: #1c1c1c;
    --grey: #555a55;
    --white: #ffffff;
  }
  * { box-sizing: border-box; margin: 0; padding: 0; }
  html, body { width: 1200px; height: 1023px; overflow: hidden; }
  body {
    background: var(--bg);
    font-family: "Roboto", Arial, sans-serif;
    position: relative;
  }
  .card {
    position: absolute;
    width: 560px;
    height: 320px;
    border-radius: 16px;
    overflow: hidden;
    box-shadow: 0 10px 26px rgba(0,0,0,.18);
  }

  /* Front */
  .card--front {
    left: 50px; top: 130px;
    background: linear-gradient(135deg, var(--card-white) 40%, var(--card-shade) 100%);
  }
  .front__decor {
    position: absolute;
    right: 40px; top: -30px;
    width: 260px; height: 260px;
    border-radius: 50%;
    background: radial-gradient(circle at 40% 40%, var(--green-pale), rgba(220,235,200,0) 70%);
  }
  .brand {
    display: flex; align-items: center; gap: 10px;
  }
  .brand__dot {
    width: 26px; height: 26px; border-radius: 50%;
    background: var(--green-mid);
    flex-shrink: 0;
  }
  .brand__name {
    font-family: "Roboto Condensed", Arial, sans-serif;
    font-weight: 700;
    color: var(--ink);
    text-transform: uppercase;
    letter-spacing: .5px;
  }
  .brand__tagline {
    font-size: 9px; color: var(--grey); margin-top: 2px;
  }
  .front__brand { position: absolute; left: 34px; top: 92px; }
  .front__brand .brand__name { font-size: 26px; line-height: 1; }
  .front__contact { position: absolute; left: 34px; top: 170px; }
  .person__name {
    font-size: 22px; font-weight: 700; color: var(--green-light);
  }
  .person__role {
    font-size: 13px; color: var(--grey); margin-bottom: 12px;
  }
  .contact-list { list-style: none; }
  .contact-list li {
    display: flex; align-items: center; gap: 8px;
    font-size: 13px; color: var(--ink); margin-bottom: 5px;
  }
  .contact-list svg { width: 13px; height: 13px; flex-shrink: 0; }

  /* Back */
  .card--back {
    left: 590px; top: 560px;
    background: var(--card-white);
  }
  .back__band { position: absolute; inset: 0; }
  .back__brand { position: absolute; right: 26px; top: 20px; }
  .back__brand .brand__name { font-size: 20px; line-height: 1; }
  .offer {
    position: absolute; right: 30px; top: 100px;
    width: 330px;
    color: var(--white);
    font-size: 12.5px; line-height: 1.35;
  }
  .offer__label {
    font-weight: 700; text-decoration: underline;
    text-align: right; font-size: 14px; margin-bottom: 2px;
  }
  .offer__question { font-weight: 700; font-size: 15px; margin-bottom: 3px; }
  .offer__list { list-style: none; margin-bottom: 6px; }
  .offer__list li::before { content: "• "; }
  .offer__closing strong { font-weight: 700; }
  .offer__amp { font-weight: 700; font-size: 15px; margin: 2px 0; }
  .offer__special strong { font-weight: 700; }
</style>
</head>
<body>

<section class="card card--front" aria-label="Business card front">
  <div class="front__decor" role="img" aria-label="Soft pale green brand decoration"></div>
  <div class="brand front__brand">
    <span class="brand__dot"></span>
    <div>
      <div class="brand__name">Liberty Path Money Coaching</div>
      <div class="brand__tagline">Reach a new level of personal freedom</div>
    </div>
  </div>
  <div class="front__contact">
    <div class="person__name">Daniel R. Hayes</div>
    <div class="person__role">Personal Financial Coach</div>
    <ul class="contact-list">
      <li>
        <svg viewBox="0 0 16 16"><circle cx="8" cy="8" r="7.5" fill="#6cba48"/><path d="M5.5 4.5l1.5 1.5-1 1c.5 1.2 1.3 2 2.5 2.5l1-1 1.5 1.5-1 1c-2.5-.3-4.7-2.5-5-5z" fill="#fff"/></svg>
        (205) 555-0187
      </li>
      <li>
        <svg viewBox="0 0 16 16"><rect x="1" y="3" width="14" height="10" rx="1" fill="#6cba48"/><path d="M1.5 3.5L8 9l6.5-5.5" stroke="#fff" stroke-width="1.3" fill="none"/></svg>
        daniel@steadymoneypath.com
      </li>
      <li>
        <svg viewBox="0 0 16 16"><circle cx="8" cy="8" r="7" fill="#6cba48"/><path d="M1 8h14M8 1c-3 3-3 11 0 14M8 1c3 3 3 11 0 14" stroke="#fff" stroke-width="1" fill="none"/></svg>
        www.steadymoneypath.com
      </li>
    </ul>
  </div>
</section>

<section class="card card--back" aria-label="Business card back">
  <svg class="back__band" viewBox="0 0 560 320" preserveAspectRatio="none" aria-hidden="true">
    <defs>
      <linearGradient id="bandFill" x1="0" y1="0" x2="1" y2="1">
        <stop offset="0" stop-color="#3f9a35"/>
        <stop offset=".6" stop-color="#6cba48"/>
        <stop offset="1" stop-color="#4fa83c"/>
      </linearGradient>
    </defs>
    <path d="M0 70 C160 80 360 70 560 105 L560 320 L0 320 Z" fill="url(#bandFill)"/>
    <path d="M0 70 C160 80 360 70 560 105" stroke="#b9dc6a" stroke-width="5" fill="none"/>
  </svg>
  <div class="brand back__brand">
    <span class="brand__dot"></span>
    <div class="brand__name">Liberty Path Money Coaching</div>
  </div>
  <div class="offer">
    <div class="offer__label">We Offer</div>
    <div class="offer__question">Struggling with your finances?</div>
    <ul class="offer__list">
      <li>Learn to become debt free</li>
      <li>Discover the power of cash</li>
      <li>Control your money instead of it controlling you</li>
    </ul>
    <p class="offer__closing">Let us help you achieve a new level of <strong>financial freedom!</strong></p>
    <p class="offer__amp">&amp;</p>
    <p class="offer__special"><strong>SPECIAL OFFER!:</strong> FREE 30 minute consultation</p>
  </div>
</section>

</body>
</html>
```